RTavenor Business Cards & Letterhead

I have a logo but need a design for some new business cards. We are a Design-Build Firm that specializes in the design and construction of commercial projects.
the cards need to be professional. no cartoon stuff.
i would like to have the cards in AI format so I can update the card as needed. Logo is provided.
Our Address is: 4187 Marlowe Ct. Fairbrook, North Carolina 27614

```html
<!DOCTYPE html>
<html lang="en">
<head>
<meta charset="utf-8">
<title>RTavenor Letterhead and Business Cards</title>
<link rel="stylesheet" href="https://fonts.googleapis.com/css2?family=Lato:wght@400;700&family=Open+Sans:wght@400;600;700&family=Parisienne&display=swap">
<style>
  :root {
    --brand-blue: #0670ad;
    --brand-grey: #6d6e70;
    --ink: #1d1d1f;
    --paper: #ffffff;
    --backdrop: #e9e6e1;
  }
  * { box-sizing: border-box; margin: 0; padding: 0; }
  html, body { width: 1200px; height: 942px; overflow: hidden; }
  body { background: var(--backdrop); position: relative; font-family: "Lato", sans-serif; color: var(--ink); }

  .letterhead {
    position: absolute; left: 84px; top: 89px; width: 541px; height: 765px;
    background: var(--paper); overflow: hidden;
    box-shadow: 0 2px 6px rgba(0,0,0,.18);
  }
  .wordmark {
    position: absolute; display: flex; align-items: center;
    font-family: "Open Sans", sans-serif; font-weight: 700; color: var(--brand-grey);
    letter-spacing: -0.01em; line-height: 1;
  }
  .wordmark .mark-square { background: var(--brand-blue); flex: none; }
  .letterhead .wordmark { left: 27px; top: 56px; font-size: 30px; }
  .letterhead .wordmark .mark-square { width: 22px; height: 22px; margin-right: 7px; }

  .contact-block {
    position: absolute; border-left: 1.5px solid var(--brand-blue);
    font-family: "Open Sans", sans-serif;
  }
  .letterhead .contact-block {
    left: 388px; top: 37px; padding-left: 9px; font-size: 9.6px; line-height: 12px;
  }
  .contact-block .address { margin-bottom: 7px; }
  .contact-line { display: flex; align-items: center; gap: 4px; white-space: nowrap; }
  .contact-line svg { flex: none; fill: var(--brand-blue); }

  .letter-body { position: absolute; left: 27px; top: 175px; width: 488px; font-size: 11.2px; line-height: 12.4px; }
  .letter-body .date { margin-bottom: 13px; }
  .letter-body .recipient { margin-bottom: 12px; }
  .letter-body .salutation { font-weight: 700; font-size: 13.5px; margin: 7px 0 16px; }
  .letter-body p.copy { text-align: justify; margin-bottom: 12px; }
  .letter-body .closing { margin-top: 28px; }
  .signature {
    position: absolute; left: 27px; top: 612px;
    font-family: "Parisienne", cursive; font-size: 26px; color: var(--ink);
  }

  .footer-band { position: absolute; left: 0; right: 0; bottom: 0; background: var(--brand-blue); }
  .footer-rule { position: absolute; left: 0; right: 0; background: var(--brand-grey); }
  .letterhead .footer-band { height: 46px; }
  .letterhead .footer-rule { bottom: 52px; height: 5px; }

  .business-card {
    position: absolute; left: 673px; width: 444px; height: 255px;
    background: var(--paper); border-radius: 20px; overflow: hidden;
    box-shadow: 0 2px 6px rgba(0,0,0,.2);
  }
  .card-front { top: 201px; }
  .card-front .wordmark { left: 36px; top: 103px; font-size: 50px; }
  .card-front .wordmark .mark-square { width: 38px; height: 38px; margin-right: 10px; }

  .card-back { top: 488px; }
  .card-back .wordmark { left: 33px; top: 114px; font-size: 27px; }
  .card-back .wordmark .mark-square { width: 20px; height: 20px; margin-right: 6px; }
  .card-back .contact-block {
    left: 257px; top: 55px; padding-left: 12px; font-size: 12.5px; line-height: 16px; color: #333;
  }
  .card-back .person-name { font-weight: 700; font-size: 17px; line-height: 19px; color: var(--brand-blue); }
  .card-back .person-title { margin-bottom: 12px; }
  .card-back .address { margin-top: 12px; margin-bottom: 0; }
  .card-back .footer-band { height: 30px; }
  .card-back .footer-rule { bottom: 35px; height: 4px; }
</style>
</head>
<body>

<section class="letterhead">
  <div class="wordmark"><span class="mark-square"></span>RTAVENOR</div>

  <div class="contact-block">
    <div class="address">4187 Marlowe Ct. Fairbrook,<br>North Carolina 27614</div>
    <div class="contact-line"><svg width="7" height="7" viewBox="0 0 10 10"><path d="M2 0l2 2.6-1.2 1.3c.6 1.4 1.7 2.5 3.2 3.2L7.3 6 10 8 9 10C4 9.6.4 6 0 1z"/></svg>555 204 7781</div>
    <div class="contact-line"><svg width="7" height="7" viewBox="0 0 10 8"><path d="M0 1h10v6H0z"/></svg>info@rtavenor-build.com</div>
    <div class="contact-line"><svg width="7" height="7" viewBox="0 0 10 10"><circle cx="5" cy="5" r="5"/></svg>www.rtavenor-build.com</div>
  </div>

  <div class="letter-body">
    <div class="date">January-03-2020</div>
    <div class="recipient">Mr, John Doe<br>President</div>
    <div class="recipient">Ferncliff Holdings<br>123 Street Name, Suite# 10<br>City, State, 120023</div>
    <div class="salutation">Dear Mr, John</div>
    <p class="copy">Lorem ipsum dolor sit amet, consectetur adipiscing elit, sed do eiusmod tempor incididunt ut labore et dolore magna aliqua. Ut enim ad minim veniam, quis nostrud exercitation ullamco laboris nisi ut aliquip ex ea commodo consequat. Duis aute irure dolor in reprehenderit in voluptate velit esse cillum dolore eu fugiat nulla pariatur.</p>
    <p class="copy">Lorem ipsum dolor sit amet, consectetur adipiscing elit, sed do eiusmod tempor incididunt ut labore et dolore magna aliqua. Ut enim ad minim veniam, quis nostrud exercitation ullamco laboris nisi ut aliquip ex ea commodo consequat. Duis aute irure dolor in reprehenderit in voluptate velit esse cillum dolore eu fugiat nulla pariatur.</p>
    <p class="copy">Lorem ipsum dolor sit amet, consectetur adipiscing elit, sed do eiusmod tempor incididunt ut labore et dolore magna aliqua. Ut enim ad minim veniam, quis nostrud exercitation ullamco laboris nisi ut aliquip ex ea commodo consequat.</p>
    <p class="copy">Excepteur sint occaecat cupidatat non proident, sunt in culpa qui officia deserunt mollit anim id est laborum. re et dolore magnam aliquam quaerat voluptatem.</p>
    <div class="closing">Regards</div>
  </div>

  <div class="signature">Daniel Hartwell</div>

  <div class="footer-rule"></div>
  <div class="footer-band"></div>
</section>

<section class="business-card card-front">
  <div class="wordmark"><span class="mark-square"></span>RTAVENOR</div>
</section>

<section class="business-card card-back">
  <div class="wordmark"><span class="mark-square"></span>RTAVENOR</div>

  <div class="contact-block">
    <div class="person-name">OWEN CALLOWAY</div>
    <div class="person-title">Managing Director</div>
    <div class="contact-line"><svg width="9" height="9" viewBox="0 0 10 10"><path d="M2 0l2 2.6-1.2 1.3c.6 1.4 1.7 2.5 3.2 3.2L7.3 6 10 8 9 10C4 9.6.4 6 0 1z"/></svg>555 204 7781</div>
    <div class="contact-line"><svg width="9" height="8" viewBox="0 0 10 8"><path d="M0 1h10v6H0z"/></svg>info@rtavenor-build.com</div>
    <div class="contact-line"><svg width="9" height="9" viewBox="0 0 10 10"><circle cx="5" cy="5" r="5"/></svg>www.rtavenor-build.com</div>
    <div class="address">4187 Marlowe Ct. Fairbrook,<br>North Carolina 27614</div>
  </div>

  <div class="footer-rule"></div>
  <div class="footer-band"></div>
</section>

</body>
</html>
```